Systems and Technology Consultants - Website

Design & Build a website for a new company which operates in the Systems and Technology space for Transportation, Government and Commercial sectors.

Overall design should be minimalist in nature.
Should also have a feed that provides news and event updates on the main page.
Logo has already been awarded and should be incorporated into the site.

We like the overall layout, functionality and simplicity of the below sites. Submitted designs could be similar to or a combination of the aspects on these sites, or perhaps a whole different concept - we are open to new ideas.
Norvique.com
Teblo.it

Update 1 Dated 27 May 2014

All I am moving away from the Teblo.it website and would like it to be more aligned with Norvique.com not only in layout but in functionality. I will be extending the deadline of this design brief for two weeks to incorporate additional requirements and will add addtional funding to the project.

Apologies for not having more information available to provide but with so many submissions its getting confusing.

Thanks Derek

Please note that the brief has been updated and the deadline has been extended.

Important: We will need two language versions of the website, English and Arabic; the website is hosted on HostPelican

Hello All, Thank you for your submissions. We have narrowed it down to the final 6 designers and I just wanted to take a moment and provide a bit of feedback regarding the concepts that we like and the modifications we are looking for. First, let me mention some of the design functions we like. - At the top of the homepage we really like the "region" or "language" tab so that the website can be viewed in both English and Arabic. - We like the homepage to have clear color variation so that the different sections of the homepage are distinct. Additionally, we like the bottom portion of the homepage to be in red. We feel that draws attention to our contact information. Again, we would like the colors to integrate black, gray-scale, red, etc. - Having a search tab at the top of the home page, or integrated into the main image, so that the site is easy to navigate. - We especially like the main image to have the scrolling tabs at the bottom so it is easy to browse the services offered (Consultancy, Solutions Architecture, Masters Systems Integration, Independent Design Review). - In regards to the services offered tab we really like the idea that a few people presented that have the outside of our logo with an icon in the middle of consultancy, solutions, etc., etc. Secondly, as mentioned in our brief we really enjoy the design of norvique site. Specially, we enjoy the strong iconic images they use, the way the tabs at the top scroll easily, and contact us page that generates an email. Lastly, I've included some photos of the concept we have been working on. What we are trying to demonstrate is how our company offers a range of services that are essentially linked together. We provide individual services that when combined present the full service package. We would like this concept to be integrated into the over concept of our website. Please feel free to ask for clarification of any of the above points or contact us if you have any additional questions. We appreciate all of your hard work and are very excited to see the updated designs. Best, Marta Vennick Quelbrant Senior Program Manager marta.vennick@quelbrant-example.com

Industry/Entity Type

Government

Font styles to use
Serif
Sans Serif

Requirements
Must have
• Must work on/adapt to various/mobile devices (responsive)
Must be simple and straightforward
Colors should be in line/matching with logo
2 language versions: English and Arabic (no Thai)
Services should be the first group/row of items after/below the main image
Note: the website will be hosted by hostpelican
Nice to have
• Submit feedback form
What's New section
The banner at the bottom of the site should not be too large; we would like a narrow one more
It would be nice if the header/top banner (with Home, About, etc. tabs) could stay in place as you scroll down (like Norvique and Chatterloop)
We will likely only use one image with a Company slogan on the Home page rather than a carousel of images to rotate through
Should not have
• This is the existing website: http://www.quelbrant-example.org
We do not like the animation, the way the banner icons/titles bounce
Not simple enough, we don't like the functionality or how pages load so slowly
We do not like the logo centered - it should be at the left
The banner and its tabs should not be towards the right, we would like them to be centered, to go all the way across and to be below the logo

```html
<!DOCTYPE html>
<html lang="en">
<head>
<meta charset="utf-8">
<title>Quelbrant – News & Events</title>
<link href="https://fonts.googleapis.com/css2?family=Open+Sans:ital,wght@0,300;0,400;0,600;1,400&display=swap" rel="stylesheet">
<style>
:root{
  --page-bg:#e9e8e8;
  --ink:#4a4a4a;
  --ink-soft:#555;
  --accent:#e3202a;
  --accent-soft:#ee7a80;
  --footer-bg:#5e5c5a;
  --footer-text:#f1f1f1;
  --divider:#cfcfcf;
}
*{margin:0;padding:0;box-sizing:border-box}
html,body{width:1037px;height:1200px;overflow:hidden}
body{font-family:"Open Sans",Arial,sans-serif;background:var(--page-bg);color:var(--ink);position:relative}
.news{position:absolute;left:0;top:0;width:1037px;height:691px;background:var(--page-bg)}
.news__title{position:absolute;top:64px;width:100%;text-align:center;font-weight:300;font-size:26px;color:var(--ink-soft);letter-spacing:.2px}
.news__intro{position:absolute;top:109px;width:100%;text-align:center;font-size:11px;line-height:19px;color:var(--ink-soft)}
.news__divider{position:absolute;left:519px;top:178px;width:1px;height:462px;background:var(--divider)}
.news__media{position:absolute;width:386px;height:140px}
.media--keyboard{left:133px;top:178px;background:linear-gradient(100deg,#3a3a3a 0%,#8a8a8a 35%,#555 60%,#2b6fc4 82%,#9fd0ff 100%)}
.media--building{left:520px;top:333px;background:linear-gradient(180deg,#8fb3d9 0%,#c9d8e6 35%,#7f9a8a 60%,#5c6a48 78%,#3f4a3c 100%)}
.media--servers{left:133px;top:487px;background:linear-gradient(90deg,#cfd6de 0%,#2a3340 25%,#4f5b6b 50%,#1f2630 75%,#3a4452 100%)}
.post{position:absolute;width:345px}
.post__date{font-size:11px;color:var(--ink)}
.post__title{margin-top:15px;font-size:11px;font-weight:400;color:var(--accent);text-transform:uppercase}
.post__body{margin-top:16px;font-size:11px;line-height:19px;color:var(--ink)}
.post__more{display:block;margin-top:9px;font-size:11px;font-style:italic;color:var(--accent);text-decoration:none}
.post--one{left:544px;top:188px}
.post--two{left:158px;top:343px}
.post--three{left:544px;top:497px}
.footer{position:absolute;left:0;top:691px;width:1037px;height:509px;background:linear-gradient(180deg,#5f5d5b 0%,#62605d 60%,#595754 100%);color:var(--footer-text)}
.footer__heading{position:absolute;top:48px;font-weight:300;font-size:15px;color:var(--accent-soft)}
.footer__text{position:absolute;font-size:11px;line-height:19px;color:var(--footer-text)}
.footer__text p+p{margin-top:16px}
.col-about{left:133px}
.col-contact{left:396px}
.col-news{left:658px}
.newsletter{position:absolute;left:658px;top:97px;width:247px;height:33px;border:1px solid #8c8a88;display:flex}
.newsletter__input{flex:1;padding-left:9px;font-size:10.5px;color:#bdbdbd;line-height:31px}
.newsletter__button{width:68px;background:var(--accent);color:#fff;font-size:10.5px;line-height:31px;text-align:center}
.connect{position:absolute;left:700px;top:205px;width:165px;text-align:center;font-weight:300;font-size:15px;color:var(--accent-soft)}
.social{position:absolute;left:679px;top:247px;display:flex;gap:17px}
.social span{width:20px;height:20px;border:1px solid #e0e0e0;border-radius:4px}
.world-map{position:absolute;left:404px;top:219px;width:228px;height:120px;border-radius:40px;background:radial-gradient(ellipse at center,rgba(255,255,255,.14) 0%,rgba(255,255,255,0) 70%)}
.brand{position:absolute;left:133px;top:412px;display:flex;align-items:center;gap:10px}
.brand__mark{width:30px;height:30px;border:3px solid var(--accent)}
.brand__name{font-size:17px;font-weight:600;letter-spacing:6px;color:var(--accent)}
.footer__tagline{position:absolute;left:396px;top:405px;width:520px;font-size:11px;line-height:19px;color:var(--footer-text)}
</style>
</head>
<body>
<section class="news">
  <h1 class="news__title">LATEST NEWS &amp; EVENTS</h1>
  <p class="news__intro">Sed ut perspiciatis unde omnis iste natus error sit voluptatem accusantium doloremque laudantium, totam rem aperiam,<br>eaque ipsa quae ab illo inventore veritatis et quasi architectobeatae vitae dicta magni dolores eos.</p>
  <div class="news__divider"></div>

  <div class="news__media media--keyboard" role="img" aria-label="Close-up photo of keyboard keys with a blue web key"></div>
  <article class="post post--one">
    <div class="post__date">18.05.2014</div>
    <h2 class="post__title">The is my tittle aliquam erat volutpat</h2>
    <p class="post__body">Cras tempor tortor turpis, sit amet bibendum ligula fermentum eget.<br>Praesent fermentum justo vitae lectus egestas.</p>
    <a class="post__more" href="#">read more</a>
  </article>

  <article class="post post--two">
    <div class="post__date">18.05.2014</div>
    <h2 class="post__title">Proin dignissim tittle</h2>
    <p class="post__body">Proin dignissim eros libero, ac facilisis leo tristique et. Ut quis tristique nisi, molestie sollicitudin mauris. Curabitur ut ullamcorper odio.</p>
    <a class="post__more" href="#">read more</a>
  </article>
  <div class="news__media media--building" role="img" aria-label="Photo of a modern glass office building beside a pond"></div>

  <div class="news__media media--servers" role="img" aria-label="Photo of server racks in a data centre"></div>
  <article class="post post--three">
    <div class="post__date">18.05.2014</div>
    <h2 class="post__title">News or event tittle</h2>
    <p class="post__body">Nullam id suscipit risus. Etiam interdum erat at imperdiet tempus. Ut<br>egestas eros eget neque congue, at hendrerit turpis tincidunt.</p>
    <a class="post__more" href="#">read more</a>
  </article>
</section>

<footer class="footer" role="contentinfo">
  <h3 class="footer__heading col-about">About us</h3>
  <div class="footer__text col-about" style="top:97px;width:250px">
    <p>Sed ut perspiciatis unde omnis iste natus error sit volup tatem accusan fames ac turpis.</p>
    <p>Doloremque laudantium, totam rem aperiam, eaque ipsa quae ab illo inventore veritatis et quasi blandit semper nibh.</p>
    <p>Nemo enim ipsam voluptatem quia voluptas sit aspernatur aut odit aut fugit, sed quia con sequun tur.</p>
  </div>

  <h3 class="footer__heading col-contact">Contact</h3>
  <div class="footer__text col-contact" style="top:97px">
    14 Orchard Lane, Meridale<br>Eastbrook, Fenwick 20480<br>Phone: +(00)-12-345-6789-0<br>E-mail: info@quelbrant-example.org
  </div>
  <div class="world-map" role="img" aria-label="Outline world map with a location pin"></div>

  <h3 class="footer__heading col-news">Newsletter</h3>
  <div class="newsletter">
    <span class="newsletter__input">email address...</span>
    <span class="newsletter__button">subscribe</span>
  </div>
  <div class="footer__text col-news" style="top:138px">Newsletter is sent monthly.</div>

  <div class="connect">Connect with us</div>
  <div class="social" aria-label="Social links"><span></span><span></span><span></span><span></span><span></span><span></span></div>

  <div class="brand"><span class="brand__mark"></span><span class="brand__name">QUELBRANT</span></div>
  <p class="footer__tagline">Sed ut perspiciatis unde omnis iste natus error sit voluptatem accusantium doloremque laudantium, totam rem aperiam, eaque ipsa quae ab illo inventore veritatis.</p>
</footer>
</body>
</html>
```